Construction business card

I need a new business card, they can connect with my logo, brand.
What we do is residential house , design and build
I like: Navy blue / black
I attached our logo, brand,
and, some idea for business card.

```html
<!DOCTYPE html>
<html lang="en">
<head>
<meta charset="utf-8">
<title>Harbrook Building Group – Business Card</title>
<link href="https://fonts.googleapis.com/css2?family=Roboto:wght@400;700&display=swap" rel="stylesheet">
<style>
  :root {
    --stage: #4b4b4d;
    --card: #262627;
    --card-deep: #1c1c1d;
    --blue: #3a86c8;
    --white: #ffffff;
    --muted: #e6e6e6;
  }
  * { margin: 0; padding: 0; box-sizing: border-box; }
  html, body {
    width: 1200px; height: 875px; overflow: hidden;
    background: var(--stage);
    font-family: "Roboto", Arial, sans-serif;
  }
  .canvas {
    position: relative; width: 1200px; height: 875px;
    display: flex; flex-direction: column; align-items: center; justify-content: center; gap: 48px;
  }
  .card {
    position: relative; width: 640px; height: 366px;
    background: var(--card); border-radius: 18px; overflow: hidden;
    box-shadow: 0 14px 30px rgba(0,0,0,.35);
  }

  /* Front */
  .card-front { display: flex; align-items: center; justify-content: center; }
  .wordmark {
    display: flex; align-items: center; gap: 12px;
    color: var(--white); font-weight: 700; text-transform: uppercase;
  }
  .wordmark-square { width: 22px; height: 22px; background: var(--blue); flex: none; }
  .card-front .wordmark { font-size: 34px; letter-spacing: 2px; }

  /* Back */
  .card-back .wordmark { position: absolute; left: 44px; top: 150px; font-size: 19px; letter-spacing: 1px; }
  .card-back .wordmark-square { width: 14px; height: 14px; }

  .person { position: absolute; right: 42px; top: 30px; text-align: right; }
  .person-name { color: var(--blue); font-weight: 700; font-size: 23px; letter-spacing: .5px; text-transform: uppercase; }
  .person-role { color: var(--white); font-size: 14px; margin-top: 2px; }
  .edge-tab { position: absolute; right: 0; top: 26px; width: 18px; height: 40px; background: var(--blue); }

  .feature-panel {
    position: absolute; right: 0; top: 120px; width: 260px; height: 200px;
    background: linear-gradient(160deg, #2e2e30 0%, var(--card-deep) 55%, #121213 100%);
    clip-path: polygon(35% 0, 100% 0, 100% 100%, 0 100%);
  }

  .contact { position: absolute; left: 92px; top: 222px; color: var(--white); font-size: 14px; line-height: 1.3; }
  .address { margin-bottom: 10px; }
  .contact-list { list-style: none; }
  .contact-list li { display: flex; align-items: center; gap: 8px; }
  .contact-list svg { width: 12px; height: 12px; flex: none; }

  .base-band { position: absolute; left: 0; bottom: 0; width: 100%; height: 14px; }
</style>
</head>
<body>
<main class="canvas">

  <section class="card card-front" aria-label="Card front">
    <div class="wordmark"><span class="wordmark-square"></span>Harbrook Building Group</div>
  </section>

  <section class="card card-back" aria-label="Card back">
    <div class="feature-panel" role="img" aria-label="Decorative dark roofline shape"></div>
    <span class="edge-tab"></span>

    <div class="person">
      <p class="person-name">Daniel Reeve</p>
      <p class="person-role">CEO/Founder</p>
    </div>

    <div class="wordmark"><span class="wordmark-square"></span>Harbrook Building Group</div>

    <div class="contact">
      <p class="address">48 Ashgrove Rd,<br>Kingsford, VIC 3150</p>
      <ul class="contact-list">
        <li>
          <svg viewBox="0 0 12 12"><path d="M3 1 L5 3.5 L4 5 Q5 7 7 8 L8.5 7 L11 9 L9.5 11 Q4 10.5 1 2.5 Z" fill="var(--blue)"/></svg>
          0400 555 182
        </li>
        <li>
          <svg viewBox="0 0 12 12"><rect x="1" y="2.5" width="10" height="7" fill="var(--blue)"/><path d="M1 2.5 L6 6.5 L11 2.5" stroke="var(--white)" fill="none"/></svg>
          info@harbrookbuild.com.au
        </li>
        <li>
          <svg viewBox="0 0 12 12"><circle cx="6" cy="6" r="5" fill="var(--blue)"/><path d="M1 6 H11 M6 1 Q3 6 6 11 M6 1 Q9 6 6 11" stroke="var(--card)" fill="none" stroke-width=".8"/></svg>
          harbrookbuild.com.au
        </li>
      </ul>
    </div>

    <svg class="base-band" viewBox="0 0 640 14" preserveAspectRatio="none" aria-hidden="true">
      <polygon points="0,4 420,4 426,14 0,14" fill="var(--blue)"/>
      <polygon points="428,0 640,0 640,14 434,14" fill="var(--white)"/>
    </svg>
  </section>

</main>
</body>
</html>
```